Wireless retailer specializing in sale / purchase of used and refurbished devices. We are an authorized dealer for " vKarma Cellular". Logos for vKarma and our logo have been included.
Business card needs to feature both locations address. We will do a reprint once we have the phone number for the second location and remove the "coming soon" text.
Cards will also need to be personalized per employee. Will post that information as well.
Any suggestions are welcome
Business
The Dial Crew
Birchwood Meadow Plaza Shopping Center
4817 Tamber Lane
Virginia Beach, VA 23464
757.318.6624
Coming in 2014
The Dial Crew 2
Marlow Quarry Shopping Center
2946 Fenwick Rd Suite #208
Virginia Beach, VA 23452

```html
<!DOCTYPE html>
<html lang="en">
<head>
<meta charset="utf-8">
<title>The Dial Crew — Business Card</title>
<link rel="stylesheet" href="https://fonts.googleapis.com/css2?family=Roboto:wght@300;500&display=swap">
<style>
  :root {
    --backdrop: #ebebeb;
    --card: #262626;
    --card-back-top: #2a2a2a;
    --card-back-bottom: #141414;
    --teal: #1a8fa8;
    --text-grey: #6f6f6f;
    --phone-grey: #5c5c5c;
    --logo-grey: #8a8a8a;
    --rule: #4a4a4a;
  }
  * { margin: 0; padding: 0; box-sizing: border-box; }
  html, body {
    width: 1200px;
    height: 900px;
    overflow: hidden;
    background: var(--backdrop);
    font-family: "Roboto", Arial, sans-serif;
  }
  .canvas {
    position: relative;
    width: 1200px;
    height: 900px;
  }
  .card {
    position: absolute;
    width: 560px;
    height: 320px;
    box-shadow: 0 6px 18px rgba(0,0,0,0.18);
  }
  /* Front */
  .card-front {
    left: 80px;
    top: 480px;
    background: var(--card);
  }
  .brand {
    position: absolute;
    left: 40px;
    top: 58px;
    display: flex;
    align-items: center;
    gap: 10px;
  }
  .brand-mark {
    width: 22px;
    height: 22px;
    background: var(--teal);
  }
  .brand-name {
    font-weight: 500;
    font-size: 30px;
    letter-spacing: 0.5px;
    text-transform: uppercase;
    color: var(--teal);
  }
  .phone {
    position: absolute;
    right: 40px;
    top: 26px;
    font-weight: 300;
    font-size: 24px;
    letter-spacing: 1px;
    color: var(--phone-grey);
  }
  .locations {
    position: absolute;
    left: 40px;
    right: 30px;
    top: 190px;
    display: flex;
  }
  .location {
    font-weight: 300;
    font-size: 13px;
    line-height: 20px;
    color: var(--text-grey);
  }
  .location-primary { width: 250px; padding-right: 18px; }
  .location-upcoming {
    padding-left: 18px;
    border-left: 1px solid var(--rule);
  }
  .location-title {
    color: var(--teal);
    text-transform: uppercase;
    font-size: 13px;
  }
  /* Back */
  .card-back {
    left: 560px;
    top: 110px;
    overflow: hidden;
  }
  .back-texture {
    position: absolute;
    inset: 0;
    background: radial-gradient(ellipse at 60% 45%, var(--card-back-top), var(--card-back-bottom));
  }
  .back-brand {
    position: absolute;
    left: 0;
    right: 0;
    top: 140px;
    display: flex;
    justify-content: center;
    align-items: center;
    gap: 10px;
  }
  .back-brand .brand-mark { background: var(--teal); width: 20px; height: 20px; }
  .back-brand .brand-name { color: var(--logo-grey); font-size: 28px; }
</style>
</head>
<body>
<main class="canvas">
  <section class="card card-back" aria-label="Card back">
    <div class="back-texture" role="img" aria-label="Dark background with a faint repeating brand-name pattern"></div>
    <div class="back-brand">
      <span class="brand-mark"></span>
      <span class="brand-name">The Dial Crew</span>
    </div>
  </section>

  <section class="card card-front" aria-label="Card front">
    <div class="phone">757.318.6624</div>
    <div class="brand">
      <span class="brand-mark"></span>
      <span class="brand-name">The Dial Crew</span>
    </div>
    <div class="locations">
      <address class="location location-primary">
        <div class="location-title">The Dial Crew</div>
        Birchwood Meadow Plaza Shopping Center<br>
        4817 Tamber Lane<br>
        Virginia Beach, VA 23464
      </address>
      <address class="location location-upcoming">
        <div class="location-title">Coming in 2014</div>
        Marlow Quarry Shopping Center<br>
        2946 Fenwick Rd Suite #208<br>
        Virginia Beach, VA 23452
      </address>
    </div>
  </section>
</main>
</body>
</html>
```